VENTURE CAPITAL GROUP BUSINESS CARD DESIGN

Venture Capital Group based in SF looking for a bold business card design. No trendy colour explosion, 3D effects etc. Just "simple" optical effects. Works on your brain, keeps your eye focused and sticks to your mind.
Target Market(s)
Technology startups
Industry/Entity Type
Venture Capital
Contact Information for Business Card
DESMOND WHITLAKE
MANAGING PARTNER
187 FENWORTH ST SAN FRANCISCO, CA 94187
415.555.0142 O
415.555.0147 F
415.555.0193 C
desmond@veldtmoorcapital.ventures

```html
<!DOCTYPE html>
<html lang="en">
<head>
<meta charset="utf-8">
<title>Veldtmoor Capital Group – Business Card</title>
<link rel="stylesheet" href="https://fonts.googleapis.com/css2?family=Open+Sans:ital,wght@0,400;0,600;0,700;1,400&display=swap">
<style>
  :root {
    --page-bg: #9b9b9b;
    --card-white: #f0f0f0;
    --brand-green: #0f6b1e;
    --brand-green-dark: #0a4d13;
    --back-green-center: #2f9a3c;
    --back-green-edge: #063f0d;
    --text-grey: #555555;
    --title-grey: #777777;
    --rule-grey: #9a9a9a;
    --disc-grey: #dcdcdc;
    --disc-grey-dark: #bdbdbd;
  }
  * { box-sizing: border-box; margin: 0; padding: 0; }
  html, body {
    width: 1105px; height: 1200px; overflow: hidden;
    background: var(--page-bg);
    font-family: "Open Sans", Arial, sans-serif;
  }
  .card {
    position: absolute;
    left: 182px;
    width: 746px;
    height: 426px;
  }
  .card--front { top: 120px; background: var(--card-white); }
  .card--back {
    top: 637px;
    background: radial-gradient(ellipse at 50% 50%, var(--back-green-center) 0%, #1a7a26 35%, var(--back-green-edge) 100%);
  }

  /* front: brand block */
  .brand {
    position: absolute;
    left: 40px; top: 108px;
    width: 282px;
    text-align: center;
  }
  .brand__disc {
    display: block;
    width: 132px; height: 132px;
    margin: 0 auto 10px;
    border-radius: 50%;
    background: radial-gradient(circle at 40% 35%, #f4f4f4, var(--disc-grey-dark));
  }
  .brand__name {
    color: var(--brand-green);
    font-weight: 400;
    font-size: 36px;
    letter-spacing: 1px;
    line-height: 1;
    text-transform: uppercase;
  }
  .brand__sub {
    color: var(--brand-green);
    font-weight: 400;
    font-size: 9px;
    letter-spacing: 3px;
    text-transform: uppercase;
    margin-top: 4px;
  }
  .card--front .brand { top: 108px; }

  .divider {
    position: absolute;
    left: 324px; top: 87px;
    width: 1px; height: 241px;
    background: var(--rule-grey);
  }

  /* front: contact block */
  .contact {
    position: absolute;
    left: 355px; top: 83px;
    color: var(--text-grey);
  }
  .contact__name {
    color: var(--brand-green);
    font-weight: 700;
    font-size: 25px;
    line-height: 1.2;
  }
  .contact__title {
    color: var(--title-grey);
    font-size: 19px;
    line-height: 1.2;
  }
  .contact__address {
    font-size: 19px;
    line-height: 1.4;
    margin-top: 12px;
  }
  .contact__lines { list-style: none; margin-top: 10px; }
  .contact__lines li {
    display: flex; align-items: center;
    font-size: 19px; line-height: 28px;
  }
  .contact__lines svg {
    width: 18px; height: 18px;
    margin-right: 10px;
    fill: var(--brand-green-dark);
    flex: none;
  }

  /* back */
  .back__disc {
    position: absolute;
    left: 268px; top: 89px;
    width: 206px; height: 206px;
    border-radius: 50%;
    background: radial-gradient(circle at 40% 35%, #f2f2f2, var(--disc-grey) 55%, var(--disc-grey-dark));
    display: flex; flex-direction: column;
    align-items: center; justify-content: center;
  }
  .back__disc .brand__name { font-size: 30px; }
  .back__url {
    position: absolute;
    left: 0; right: 0; top: 348px;
    text-align: center;
    color: #ffffff;
    font-style: italic;
    font-size: 20px;
    letter-spacing: 1.5px;
  }
</style>
</head>
<body>

<section class="card card--front">
  <div class="brand">
    <span class="brand__disc"></span>
    <div class="brand__name">Veldtmoor</div>
    <div class="brand__sub">Capital Group</div>
  </div>

  <div class="divider"></div>

  <div class="contact">
    <div class="contact__name">Desmond Whitlake</div>
    <div class="contact__title">Managing Partner</div>
    <div class="contact__address">187 Fenworth ST San Francisco<br>CA 94187</div>
    <ul class="contact__lines">
      <li>
        <svg viewBox="0 0 24 24" aria-hidden="true"><path d="M6.6 10.8c1.4 2.8 3.8 5.1 6.6 6.6l2.2-2.2c.3-.3.7-.4 1-.2 1.1.4 2.3.6 3.6.6.6 0 1 .4 1 1V20c0 .6-.4 1-1 1C10.6 21 3 13.4 3 4c0-.6.4-1 1-1h3.5c.6 0 1 .4 1 1 0 1.3.2 2.5.6 3.6.1.3 0 .7-.2 1z"/></svg>
        415.555.0142
      </li>
      <li>
        <svg viewBox="0 0 24 24" aria-hidden="true"><path d="M7 1h10c1.1 0 2 .9 2 2v18c0 1.1-.9 2-2 2H7c-1.1 0-2-.9-2-2V3c0-1.1.9-2 2-2zm0 3v14h10V4H7zm5 15.2a1.2 1.2 0 1 0 0 2.4 1.2 1.2 0 0 0 0-2.4z"/></svg>
        415.555.0193
      </li>
      <li>
        <svg viewBox="0 0 24 24" aria-hidden="true"><path d="M6 2h10l2 2v5H6zM3 10h18c1.1 0 2 .9 2 2v6h-4v4H5v-4H1v-6c0-1.1.9-2 2-2zm4 7v3h10v-3z"/></svg>
        415.555.0147
      </li>
      <li>
        <svg viewBox="0 0 24 24" aria-hidden="true"><path d="M2 5h20v14H2zm2 2v.5l8 5 8-5V7zm0 2.8V17h16V9.8l-8 5z"/></svg>
        desmond@veldtmoorcapital.ventures
      </li>
    </ul>
  </div>
</section>

<section class="card card--back">
  <div class="back__disc">
    <div class="brand__name">Veldtmoor</div>
  </div>
  <div class="back__url">www.veldtmoorcapital.ventures</div>
</section>

</body>
</html>
```